Fire Risk Assessment App needs a sleek UI design

I need a sleek, modern but professional design for my 5 page Fire Risk Assessment App. Include gradient background, fire themed colours including reds, yellows, light orange and a touch of black. Design must ooze simplicity and professionalism. This is for the UK market. See attached images and word doc for more information.

Target Market(s)

General public and business owners

Industry/Entity Type

Technology / Fire Safety

Colors
00AB8E
00BBA5
67D7C9
C6EFE9
E9F9F6
59FF00
82FF00
B8FF75
E3FFCB
F4FFEA
FFC000
F8CF3A
FAE287
FDF2CF
FEFAEE
F0912C
F2A743
F7CA91
FBE8D2
FDF5EE
EE7325
F08F49
F5BC92
FAE3D3
FDF4ED
EB3D1F
EC4F4E
F09395
F8D3D4
FCEDEE

```html
<!DOCTYPE html>
<html lang="en">
<head>
<meta charset="utf-8">
<title>Fire Risk Assessment App – Screens</title>
<link href="https://fonts.googleapis.com/css2?family=Poppins:wght@300;400;500;600&display=swap" rel="stylesheet">
<style>
:root{
  --bg-top:#F2A743;
  --bg-bottom:#F0912C;
  --screen:#F8F6F3;
  --screen-warm:#FBE8D2;
  --ink:#2a2a2a;
  --ink-soft:#555;
  --muted:#9a9a9a;
  --green:#3DB81E;
  --green-dark:#2E9A14;
  --red:#E8242A;
  --amber:#F8A81C;
  --gold:#F8CF3A;
  --ring:#2FBF3A;
  --orange:#F0912C;
  --nav:#7a8088;
  --card:#ffffff;
}
*{box-sizing:border-box;margin:0;padding:0}
html,body{width:1200px;height:442px;overflow:hidden}
body{
  background:linear-gradient(180deg,var(--bg-top),var(--bg-bottom));
  font-family:'Poppins',sans-serif;color:var(--ink);position:relative;
}
.screen{
  position:absolute;top:56px;width:160px;height:348px;border-radius:18px;overflow:hidden;
  background:linear-gradient(180deg,var(--screen) 0%,var(--screen) 70%,var(--screen-warm) 100%);
  box-shadow:0 6px 14px rgba(120,50,0,.25);
}
.abs{position:absolute}
.center{left:0;right:0;text-align:center}
.heading{display:flex;align-items:center;justify-content:center;gap:4px;font-size:8px;font-weight:400;top:24px;left:0;right:0}
.btn{position:absolute;color:#fff;font-size:7px;font-weight:500;border-radius:3px;display:flex;align-items:center;box-shadow:0 1px 2px rgba(0,0,0,.2)}
.btn-green{background:var(--green)}
.btn-red{background:var(--red)}
.btn-amber{background:var(--amber)}
.btn-gold{background:var(--gold);color:var(--ink)}
.placeholder{position:absolute;border-radius:3px}
.nav{position:absolute;left:0;right:0;bottom:0;height:26px;background:#fff;display:flex;justify-content:space-around;align-items:center;padding:0 8px}
.nav svg{width:12px;height:12px;color:var(--nav)}
.nav .active-green{color:var(--green)}
.nav .active-orange{color:var(--orange)}
/* intro */
.intro-title{top:26px;font-size:7.6px;line-height:1.4}
.intro-copy{font-size:7.6px;line-height:1.4}
.footer-note{font-size:5.8px;color:var(--ink-soft)}
/* dashboard */
.type-label{font-size:5.8px;color:var(--ink-soft);text-align:center;width:40px}
.type-icon{width:26px;height:26px;border-radius:50%;background:#fff;box-shadow:0 1px 3px rgba(0,0,0,.2);display:flex;align-items:center;justify-content:center}
.status{width:78px;height:16px;padding:0 8px;justify-content:space-between}
.site{left:17px;display:flex;align-items:center;gap:5px;font-size:6.6px}
.site i{width:7px;height:8px;background:#b9c7d8;border-radius:1px;display:block}
/* question */
.q-meta{left:16px;font-size:6.6px;line-height:1.6;color:var(--ink)}
.ring-label{font-size:4.6px;text-align:center;width:30px;color:var(--ink-soft)}
.answer-box{left:16px;width:127px;height:30px;background:#fff;border-radius:2px;font-size:5.8px;color:var(--ink-soft);padding:5px 7px}
/* purchase */
.tier{left:16px;width:127px;height:54px;background:var(--card);border-radius:3px;box-shadow:0 1px 3px rgba(0,0,0,.06)}
.tier-name{position:absolute;left:19px;top:5px;font-size:7px;font-weight:500}
.tier-sub{position:absolute;left:19px;top:14px;font-size:5.2px;color:var(--ink-soft)}
.tier-dot{position:absolute;left:8px;top:7px;width:8px;height:8px;border-radius:50%}
.tier-was{position:absolute;right:12px;top:5px;font-size:5.4px;color:var(--ink-soft);text-decoration:line-through}
.tier-price{position:absolute;right:10px;top:11px;font-size:7.4px;font-weight:500}
.tier-price.solo{top:9px}
.tier .btn{left:42px;top:30px;width:44px;height:16px;justify-content:center}
/* support */
.support-label{left:16px;top:58px;font-size:6.4px;color:var(--ink-soft)}
.support-box{left:16px;top:71px;width:126px;height:71px;background:#fff;border-radius:2px;font-size:5px;color:var(--muted);padding:6px 7px}
</style>
</head>
<body>
<svg width="0" height="0" style="position:absolute" aria-hidden="true">
  <defs>
    <symbol id="i-gauge" viewBox="0 0 24 24"><circle cx="12" cy="12" r="10" fill="none" stroke="currentColor" stroke-width="2"/><path d="M12 12 L16 7" stroke="currentColor" stroke-width="2" stroke-linecap="round"/></symbol>
    <symbol id="i-card" viewBox="0 0 24 24"><rect x="2" y="5" width="20" height="14" rx="2" fill="currentColor"/><rect x="2" y="9" width="20" height="3" fill="#fff"/></symbol>
    <symbol id="i-chat" viewBox="0 0 24 24"><path d="M3 4h18v12H9l-5 4v-4H3z" fill="currentColor"/><path d="M7 8h10M7 12h7" stroke="#fff" stroke-width="1.6"/></symbol>
    <symbol id="i-exit" viewBox="0 0 24 24"><circle cx="14" cy="4" r="2" fill="currentColor"/><path d="M13 7 L9 13 L13 15 L11 22 M10 10 L6 12 M12 9 L17 12 M9 13 L5 20" stroke="currentColor" stroke-width="2" fill="none" stroke-linecap="round"/></symbol>
    <symbol id="i-mic" viewBox="0 0 24 24"><rect x="8" y="2" width="8" height="13" rx="4" fill="currentColor"/><path d="M5 11a7 7 0 0 0 14 0M12 18v4" stroke="currentColor" stroke-width="2" fill="none"/></symbol>
  </defs>
</svg>

<!-- Screen: welcome -->
<section class="screen" style="left:69px">
  <p class="abs center intro-title">The most ‘user-friendly’ Fire Risk<br>Assessment App available.</p>
  <div class="placeholder" role="img" aria-label="Stacked preview cards of the assessment question screen" style="left:24px;top:54px;width:110px;height:98px;background:linear-gradient(160deg,#ffffff,#efe9e2)"></div>
  <p class="abs center intro-copy" style="top:162px">Quick tap responses and<br>voice-activated typing.</p>
  <svg class="abs" style="left:75px;top:186px;width:9px;height:11px;color:#999"><use href="#i-mic"/></svg>
  <div class="btn btn-green" style="left:16px;top:203px;width:127px;height:20px;padding-left:16px;gap:8px">
    <svg width="9" height="9" viewBox="0 0 24 24"><circle cx="12" cy="8" r="4" fill="none" stroke="#fff" stroke-width="2"/><path d="M4 22c0-5 4-8 8-8s8 3 8 8z" fill="none" stroke="#fff" stroke-width="2"/></svg>
    Create a Free account</div>
  <p class="abs center intro-copy" style="top:235px">Any Responsible Person can do it.</p>
  <div class="btn btn-red" style="left:16px;top:255px;width:127px;height:20px;padding-left:16px;gap:20px">
    <svg width="9" height="9" viewBox="0 0 24 24"><circle cx="12" cy="12" r="10" fill="none" stroke="#fff" stroke-width="2"/><path d="M7 12h9M12 8l4 4-4 4" stroke="#fff" stroke-width="2" fill="none"/></svg>
    Customer Log in</div>
  <div class="placeholder" role="img" aria-label="Fingerprint login icon" style="left:68px;top:287px;width:24px;height:30px;background:linear-gradient(180deg,#ffffff,#dcdcdc)"></div>
  <p class="abs center footer-note" style="top:326px">Created and endorsed by British Firefighters.</p>
</section>

<!-- Screen: dashboard -->
<section class="screen" style="left:291px">
  <div class="abs heading"><svg width="11" height="11" style="color:#555"><use href="#i-gauge"/></svg>DASHBOARD</div>
  <p class="abs center" style="top:48px;font-size:6px;font-weight:500">Start Fire Risk Assessment</p>
  <svg class="abs" style="left:0;top:58px" width="160" height="60">
    <circle cx="81" cy="14" r="13" fill="var(--red)"/>
    <path d="M81 7v14M74 14h14" stroke="#fff" stroke-width="2.4"/>
    <path d="M76 28 L58 44 M86 28 L104 44" stroke="#555" stroke-width=".8" stroke-dasharray="1.5 1.5"/>
  </svg>
  <div class="abs type-icon" style="left:41px;top:101px" role="img" aria-label="Commercial building icon"><i style="width:10px;height:13px;background:#b9c7d8;display:block;border-radius:1px"></i></div>
  <div class="abs type-icon" style="left:93px;top:101px" role="img" aria-label="Residential house icon"><i style="width:12px;height:10px;background:#d9a07a;display:block;border-radius:1px"></i></div>
  <p class="abs type-label" style="left:34px;top:131px">Commercial</p>
  <p class="abs type-label" style="left:86px;top:131px">Residential</p>

  <div class="btn btn-green status" style="left:17px;top:151px">Complete
    <svg width="7" height="7" viewBox="0 0 24 24"><circle cx="12" cy="12" r="11" fill="#fff"/><path d="M7 12l3 3 6-6" stroke="var(--green)" stroke-width="3" fill="none"/></svg></div>
  <p class="abs site" style="top:175px;font-size:7.2px"><i></i>Leo's Barbershop</p>
  <div class="btn btn-amber status" style="left:17px;top:193px">In Progress
    <svg width="7" height="7" viewBox="0 0 24 24"><circle cx="12" cy="12" r="9" fill="none" stroke="#fff" stroke-width="3" stroke-dasharray="40 20"/></svg></div>
  <p class="abs site" style="top:217px"><i></i>Elm Rd School</p>
  <p class="abs site" style="top:231px"><i></i>Oakfield Nursing Home</p>
  <div class="btn btn-red status" style="left:17px;top:251px">Purchases
    <svg width="9" height="8" viewBox="0 0 24 20"><path d="M1 2h4l3 11h12l3-8H7" stroke="#fff" stroke-width="2" fill="none"/><circle cx="10" cy="17" r="2" fill="#fff"/><circle cx="18" cy="17" r="2" fill="#fff"/></svg></div>
  <p class="abs site" style="top:274px"><i style="background:#d9a07a"></i>Residential Fire Risk Assessment</p>
  <p class="abs site" style="top:288px"><i></i>Commercial Fire Risk Assessment</p>
  <p class="abs site" style="top:302px"><i></i>Commercial Fire Risk Assessment</p>
  <nav class="nav">
    <svg><use href="#i-gauge"/></svg><svg><use href="#i-card"/></svg><svg><use href="#i-chat"/></svg><svg><use href="#i-exit"/></svg>
  </nav>
</section>

<!-- Screen: assessment question -->
<section class="screen" style="left:518px">
  <p class="abs q-meta" style="top:27px;font-size:7.6px;line-height:1.4">Fire Risk ASSESSMENT<br>FIRE HAZARDS</p>
  <p class="abs q-meta" style="top:53px">SECTION 7.00/30.00</p>
  <p class="abs q-meta" style="top:67px;line-height:1.6">ELECTRONIC SOURCES<br>OF IGNITION<br>(Clause 13 &amp; Annex B)</p>
  <svg class="abs" style="left:122px;top:27px" width="22" height="22" viewBox="0 0 22 22"><circle cx="11" cy="11" r="9" fill="none" stroke="var(--ring)" stroke-width="2.4" stroke-dasharray="44 13" transform="rotate(-60 11 11)"/></svg>
  <p class="abs ring-label" style="left:118px;top:52px">Section<br>Progress</p>
  <svg class="abs" style="left:122px;top:72px" width="22" height="22" viewBox="0 0 22 22"><circle cx="11" cy="11" r="9" fill="none" stroke="var(--ring)" stroke-width="2.4" stroke-dasharray="44 13" transform="rotate(-60 11 11)"/></svg>
  <p class="abs ring-label" style="left:118px;top:96px">Assessment<br>Progress</p>
  <svg class="abs" style="left:70px;top:111px" width="20" height="20" viewBox="0 0 24 24"><circle cx="12" cy="12" r="10" fill="none" stroke="#333" stroke-width="1.4"/><path d="M13 3 L7 13h5l-2 8 7-11h-5z" fill="var(--gold)"/></svg>
  <p class="abs q-meta" style="top:139px;font-size:7.6px">Q:7.01</p>
  <p class="abs q-meta" style="top:150px;font-size:7px;line-height:1.45;width:130px">Are reasonable measures taken to prevent fires of electrical origin?</p>
  <svg class="abs" style="left:24px;top:177px" width="115" height="13" viewBox="0 0 115 13">
    <circle cx="6" cy="6.5" r="5.5" fill="none" stroke="var(--green)" stroke-width="1"/><path d="M3.5 6.5l2 2 3.5-4" stroke="var(--green)" fill="none"/>
    <circle cx="29" cy="6.5" r="5.5" fill="none" stroke="var(--red)" stroke-width="1"/><path d="M26.5 4l5 5M31.5 4l-5 5" stroke="var(--red)"/>
    <circle cx="53" cy="6.5" r="5.5" fill="none" stroke="var(--amber)" stroke-width="1"/><path d="M50 6.5h6" stroke="var(--amber)"/>
    <rect x="74" y="1" width="4" height="7" rx="2" fill="#333"/><path d="M72.5 6a3.5 3.5 0 0 0 7 0M76 10v2.5" stroke="#333" fill="none"/>
    <rect x="94" y="3" width="13" height="9" rx="1.5" fill="#333"/><rect x="97" y="1.5" width="5" height="2" fill="#333"/><circle cx="100.5" cy="7.5" r="2.5" fill="#fff"/>
  </svg>
  <p class="abs answer-box" style="top:201px">No, electric sockets are overloaded</p>
  <div class="placeholder" role="img" aria-label="Photo of an overloaded multi-socket adapter" style="left:34px;top:240px;width:92px;height:48px;background:linear-gradient(180deg,#d8dde2,#c4cad0)"></div>
  <div class="btn btn-gold" style="left:16px;top:297px;width:61px;height:17px;justify-content:center">Save + Close</div>
  <div class="btn btn-green" style="left:82px;top:297px;width:61px;height:17px;justify-content:center">Next »</div>
  <nav class="nav">
    <svg><use href="#i-gauge"/></svg><svg><use href="#i-card"/></svg><svg><use href="#i-chat"/></svg><svg><use href="#i-exit"/></svg>
  </nav>
</section>

<!-- Screen: purchase options -->
<section class="screen" style="left:744px">
  <div class="abs heading"><svg width="12" height="10" style="color:var(--green)"><use href="#i-card"/></svg>PURCHASE OPTIONS</div>
  <article class="abs tier" style="top:49px">
    <span class="tier-dot" style="background:#c98a52"></span>
    <p class="tier-name">Bronze</p><p class="tier-sub">1 Fire Risk Assessment</p>
    <p class="tier-price solo">£19.99</p>
    <div class="btn btn-green">Puchase</div>
  </article>
  <article class="abs tier" style="top:110px">
    <span class="tier-dot" style="background:#a7adb5"></span>
    <p class="tier-name">Silver</p><p class="tier-sub">3 Fire Risk Assessment</p>
    <p class="tier-was">£59.97</p><p class="tier-price">£54.99</p>
    <div class="btn btn-green">Puchase</div>
  </article>
  <article class="abs tier" style="top:171px">
    <span class="tier-dot" style="background:#e0a64a"></span>
    <p class="tier-name">Gold</p><p class="tier-sub">5 Fire Risk Assessment</p>
    <p class="tier-was">£99.95</p><p class="tier-price">£89.99</p>
    <div class="btn btn-green">Puchase</div>
  </article>
  <article class="abs tier" style="top:233px">
    <span class="tier-dot" style="background:#9aa6bf"></span>
    <p class="tier-name">Platinum</p><p class="tier-sub">10 Fire Risk Assessment</p>
    <p class="tier-was">£199.90</p><p class="tier-price">£174.99</p>
    <div class="btn btn-green">Puchase</div>
  </article>
  <nav class="nav">
    <svg><use href="#i-gauge"/></svg><svg class="active-green"><use href="#i-card"/></svg><svg><use href="#i-chat"/></svg><svg><use href="#i-exit"/></svg>
  </nav>
</section>

<!-- Screen: technical support -->
<section class="screen" style="left:971px">
  <div class="abs heading"><svg width="11" height="11" style="color:var(--orange)"><use href="#i-chat"/></svg>TECHNICAL SUPPORT</div>
  <p class="abs support-label">Type/record your response here</p>
  <svg class="abs" style="left:135px;top:56px;width:8px;height:10px;color:#999"><use href="#i-mic"/></svg>
  <p class="abs support-box">Type here</p>
  <nav class="nav">
    <svg><use href="#i-gauge"/></svg><svg><use href="#i-card"/></svg><svg class="active-orange"><use href="#i-chat"/></svg><svg><use href="#i-exit"/></svg>
  </nav>
</section>
</body>
</html>
```